Business Card Re-Design/Update

We'd like to update out business cards. I've included our current "Style guide" which has the colour scheme of the organisation in it. I've also included the branding files with logos etc in them.

I've also included a copy of one of our existing cards so that you can see how ugly/dated they look. I'd like a fresh modern corporate look.

Target Market(s)

These are for our clients, potential clients, industry contacts - like all business cards

Contact Information for Business Card

Name
Position
Company Address - Level 1, 47 Fernby Street, Carlow Qld 4072
Direct Phone
mobile
Email
Website -www.korvalit.com.au
Logo

Colors

Designer to choose colors to be used in the design.

Requirements
Must have
• Main Logo
• Cards will need to be editable to be able to personalize them for each new employee.
Nice to have
• The MapOut, ShipWell, KeepSteady would be okay to have if they can be sensibly and professionally added to the look without detracting from the main imagery.
• Maybe they could go on the back of the card? will leave this to your creative discretion as to whether/where they fit.
Should not have
• Should not have decorative or script fonts

```html
<!DOCTYPE html>
<html lang="en">
<head>
<meta charset="utf-8">
<title>korvalIT business card</title>
<link rel="stylesheet" href="https://fonts.googleapis.com/css2?family=Roboto:wght@400;500;700&display=swap">
<style>
  :root {
    --brand-red: #d0161e;
    --brand-red-deep: #a80d12;
    --ink: #2a2a2a;
    --ink-soft: #555555;
    --paper: #f7f7f7;
    --tile: #efefef;
    --stage: #e4e2df;
  }
  * { box-sizing: border-box; margin: 0; padding: 0; }
  html, body { width: 1200px; height: 911px; overflow: hidden; }
  body {
    background: var(--stage);
    font-family: "Roboto", Arial, sans-serif;
    position: relative;
  }
  .card {
    position: absolute;
    width: 540px;
    height: 309px;
    top: 301px;
    border-radius: 3px;
    overflow: hidden;
    box-shadow: 0 10px 24px rgba(0,0,0,0.18);
  }
  .card--front { left: 40px; background: var(--paper); }
  .card--back {
    left: 620px;
    background: linear-gradient(135deg, var(--brand-red) 0%, var(--brand-red-deep) 100%);
  }
  .front-art { position: absolute; inset: 0; }
  .front-details {
    position: absolute;
    left: 28px;
    bottom: 24px;
    width: 225px;
    color: var(--ink);
  }
  .wordmark {
    display: flex;
    align-items: center;
    gap: 8px;
    font-size: 24px;
    font-weight: 700;
    color: var(--ink);
    margin-bottom: 8px;
  }
  .wordmark-square {
    width: 16px; height: 16px;
    background: var(--brand-red);
  }
  .person-name {
    font-size: 16px;
    font-weight: 700;
    color: var(--brand-red);
    text-transform: uppercase;
    letter-spacing: 0.01em;
  }
  .person-role {
    font-size: 11px;
    font-weight: 700;
    color: var(--ink);
    margin-bottom: 7px;
  }
  .address {
    font-size: 11px;
    color: var(--ink-soft);
    line-height: 1.35;
    margin-bottom: 5px;
  }
  .contact-list { list-style: none; }
  .contact-list li {
    display: flex;
    align-items: center;
    gap: 7px;
    font-size: 11px;
    color: var(--ink-soft);
    line-height: 1.42;
  }
  .contact-icon { width: 10px; height: 10px; flex: none; }
  .back-brand {
    position: absolute;
    left: 0; right: 0; top: 96px;
    display: flex;
    justify-content: center;
    align-items: center;
    gap: 12px;
    color: #ffffff;
    font-size: 40px;
    font-weight: 700;
  }
  .back-brand-square {
    width: 30px; height: 30px;
    border: 5px solid #ffffff;
  }
  .taglines {
    position: absolute;
    left: 30px;
    bottom: 26px;
    display: flex;
    align-items: center;
    gap: 12px;
    color: #ffffff;
    font-size: 16px;
    font-weight: 500;
  }
  .tagline-divider {
    width: 1px; height: 16px;
    background: rgba(255,255,255,0.7);
  }
</style>
</head>
<body>

<section class="card card--front" aria-label="Card front">
  <svg class="front-art" width="540" height="309" viewBox="0 0 540 309">
    <defs>
      <linearGradient id="frontRed" x1="0" y1="0" x2="1" y2="1">
        <stop offset="0" stop-color="#d0161e"/>
        <stop offset="1" stop-color="#a80d12"/>
      </linearGradient>
    </defs>
    <polygon class="front-band" points="268,0 540,0 540,150 425,240 268,240" fill="url(#frontRed)"/>
    <rect class="front-tile" x="292" y="0" width="178" height="212" fill="#efefef"/>
  </svg>

  <div class="front-details">
    <div class="wordmark"><span class="wordmark-square"></span>korvalIT</div>
    <p class="person-name">Maren Holt</p>
    <p class="person-role">Business Development Manager</p>
    <p class="address">Level 1, 47 Fernby Street<br>Carlow Qld 4072</p>
    <ul class="contact-list">
      <li>
        <svg class="contact-icon" viewBox="0 0 10 10"><path d="M2 0.5 L4 2.5 L3 4 Q4.5 6 6 7 L7.5 6 L9.5 8 L8 9.5 Q3 9 0.5 2 Z" fill="#d0161e"/></svg>
        +61 (0)7 3148 2260
      </li>
      <li>
        <svg class="contact-icon" viewBox="0 0 10 10"><path d="M2 0.5 L4 2.5 L3 4 Q4.5 6 6 7 L7.5 6 L9.5 8 L8 9.5 Q3 9 0.5 2 Z" fill="#d0161e"/></svg>
        +61 (0)7 3148 2274
      </li>
      <li>
        <svg class="contact-icon" viewBox="0 0 10 10"><rect x="2.5" y="0.5" width="5" height="9" rx="1" fill="none" stroke="#d0161e" stroke-width="1.2"/></svg>
        +61 (0)412 907 318
      </li>
      <li>
        <svg class="contact-icon" viewBox="0 0 10 10"><rect x="1" y="3" width="8" height="6" fill="#d0161e"/><rect x="2.5" y="0.5" width="5" height="3" fill="none" stroke="#d0161e"/></svg>
        +61 (0)7 3148 2299
      </li>
      <li>
        <svg class="contact-icon" viewBox="0 0 10 10"><rect x="0.5" y="2" width="9" height="6.5" fill="#d0161e"/><path d="M0.5 2 L5 5.5 L9.5 2" fill="none" stroke="#ffffff" stroke-width="1"/></svg>
        mholt@korvalit.com.au
      </li>
      <li>
        <svg class="contact-icon" viewBox="0 0 10 10"><circle cx="5" cy="5" r="4.5" fill="#d0161e"/></svg>
        www.korvalit.com.au
      </li>
    </ul>
  </div>
</section>

<section class="card card--back" aria-label="Card back">
  <div class="back-brand"><span class="back-brand-square"></span>korvalIT</div>
  <div class="taglines">
    <span>MapOut</span>
    <span class="tagline-divider"></span>
    <span>ShipWell</span>
    <span class="tagline-divider"></span>
    <span>KeepSteady</span>
  </div>
</section>

</body>
</html>
```